Harbourline Electrical Solutions

On one side. LOGO (underneath:) Commercial Industrial Residential

- NAME & CONTACT DETAILS

Marcus T. Hollings
Project Manager

(Cell icon) (441) 555-0187
(Email icon) hlelectricalsolutions@mailvento.com
(Facebook & Instagram icons )@hlelectricalsolutions

Other side: LOGO - underneath ELECTRICAL CONSTRUCTION & MAINTENANCE . LED LIGHTING & AUTOMATION . LIFE SAFETY SYSTEMS (FIRE ALARM / SECURITY) . DATA & COMMUNICATION

```html
<!DOCTYPE html>
<html lang="en">
<head>
<meta charset="utf-8">
<title>Harbourline Electrical Solutions – Business Card</title>
<link href="https://fonts.googleapis.com/css2?family=Montserrat:wght@500;600&family=Work+Sans:wght@400;500&display=swap" rel="stylesheet">
<style>
  :root {
    --backdrop: #2b2b2d;
    --card-dark: #161616;
    --card-light: #ffffff;
    --teal: #1d5c70;
    --ink: #1b4f63;
    --grey: #5a5a5a;
    --white: #ffffff;
  }
  * { box-sizing: border-box; margin: 0; padding: 0; }
  html, body {
    width: 1200px; height: 900px; overflow: hidden;
    background: var(--backdrop);
  }
  .canvas {
    position: relative; width: 1200px; height: 900px;
  }
  .card {
    position: absolute; left: 250px; width: 700px; height: 400px;
    border-radius: 22px; overflow: hidden;
  }

  /* Back side */
  .card--back { top: 36px; background: var(--card-dark); color: var(--white); }
  .back-brand {
    position: absolute; top: 70px; left: 0; right: 0;
    display: flex; align-items: center; justify-content: center; gap: 22px;
  }
  .brand-square {
    width: 46px; height: 46px; background: var(--white);
  }
  .back-brand .brand-name {
    font-family: "Montserrat", sans-serif; font-weight: 600;
    font-size: 30px; letter-spacing: 4px; line-height: 1.25;
    text-transform: uppercase; color: var(--white);
  }
  .service-list {
    position: absolute; top: 220px; left: 110px;
    list-style: none;
    font-family: "Montserrat", sans-serif; font-weight: 600;
    font-size: 19px; letter-spacing: 1.6px; line-height: 1.45;
    text-transform: uppercase;
  }
  .service-list li::before {
    content: ""; display: inline-block; width: 7px; height: 7px;
    border-radius: 50%; background: var(--white);
    margin: 0 16px 4px -23px; vertical-align: middle;
  }

  /* Front side */
  .card--front { top: 466px; background: var(--card-light); }
  .front-brand {
    position: absolute; top: 46px; left: 52px;
    display: flex; align-items: center; gap: 14px;
  }
  .front-brand .brand-square { width: 34px; height: 34px; background: var(--teal); }
  .front-brand .brand-name {
    font-family: "Montserrat", sans-serif; font-weight: 600;
    font-size: 16px; letter-spacing: 2.4px; line-height: 1.2;
    text-transform: uppercase; color: var(--teal);
  }
  .social {
    position: absolute; top: 228px; left: 52px;
    font-family: "Work Sans", sans-serif; font-size: 20px;
    color: var(--grey); letter-spacing: 0.4px;
  }
  .divider-left {
    position: absolute; top: 262px; left: 52px; width: 596px;
    height: 2px; background: var(--teal);
  }
  .person {
    position: absolute; top: 278px; right: 52px; text-align: right;
  }
  .person-name {
    font-family: "Montserrat", sans-serif; font-weight: 600;
    font-size: 26px; letter-spacing: 1.2px; color: var(--ink);
    text-transform: uppercase;
  }
  .person-role {
    font-family: "Work Sans", sans-serif; font-size: 19px;
    color: var(--grey); margin-top: 2px; letter-spacing: 0.5px;
  }
  .contact {
    position: absolute; top: 342px; right: 52px; text-align: right;
    list-style: none;
    font-family: "Work Sans", sans-serif; font-size: 18px;
    color: var(--grey); line-height: 1.45; letter-spacing: 0.4px;
  }
  .contact li { display: flex; justify-content: flex-end; align-items: center; gap: 12px; }
  .contact svg { width: 17px; height: 17px; flex: none; }
</style>
</head>
<body>
<main class="canvas">

  <section class="card card--back" aria-label="Card back">
    <div class="back-brand">
      <span class="brand-square"></span>
      <p class="brand-name">Harbourline<br>Electrical<br>Solutions</p>
    </div>
    <ul class="service-list">
      <li>Data &amp; Communication</li>
      <li>LED Lighting &amp; Automation</li>
      <li>Electrical Construction &amp; Maintenance</li>
      <li>Life Safety Systems (Fire Alarm / Security)</li>
    </ul>
  </section>

  <section class="card card--front" aria-label="Card front">
    <div class="front-brand">
      <span class="brand-square"></span>
      <p class="brand-name">Harbourline<br>Electrical<br>Solutions</p>
    </div>

    <p class="social">@hlelectricalsolutions</p>
    <div class="divider-left"></div>

    <div class="person">
      <p class="person-name">Marcus T. Hollings</p>
      <p class="person-role">Project Manager</p>
    </div>

    <ul class="contact">
      <li>(441) 555-0187
        <svg viewBox="0 0 24 24" aria-hidden="true"><path d="M6.6 10.8a15 15 0 0 0 6.6 6.6l2.2-2.2a1 1 0 0 1 1-.25 11.4 11.4 0 0 0 3.6.6 1 1 0 0 1 1 1V20a1 1 0 0 1-1 1A17 17 0 0 1 3 4a1 1 0 0 1 1-1h3.5a1 1 0 0 1 1 1c0 1.25.2 2.45.6 3.6a1 1 0 0 1-.25 1z" fill="var(--teal)"/></svg>
      </li>
      <li>hlelectricalsolutions@mailvento.com
        <svg viewBox="0 0 24 24" aria-hidden="true"><rect x="2.5" y="5" width="19" height="14" rx="1.5" fill="none" stroke="var(--teal)" stroke-width="2"/><path d="M3 6l9 7 9-7" fill="none" stroke="var(--teal)" stroke-width="2"/></svg>
      </li>
    </ul>
  </section>

</main>
</body>
</html>
```